SkyvornQ Business Cards and Stationary Design

Need a design for our business cards and stationary. I want to carry on the theme of the logo. I want the business cards to have a design on the back. I would like the business cards and the stationary to carry the same theme, design scheme, and branding

Target Market(s)

Airlines and Maintenance Facilities

Industry/Entity Type

Aviation

Contact Information for Business Card

Name
Position Title
Address: 4827 Trellis Hollow Road, Fort Pierce, Florida, 34951
Office Number
Mobile Number
Email
Website

Font styles to use
Serif
Sans Serif

Colors

Designer to choose colors to be used in the design.

```html
<!DOCTYPE html>
<html lang="en">
<head>
<meta charset="utf-8">
<title>SkyvornQ Business Card</title>
<link rel="stylesheet" href="https://fonts.googleapis.com/css2?family=Roboto:wght@400;500;700&display=swap">
<style>
  :root {
    --backdrop: #2e2e2e;
    --card-white: #f4f4f4;
    --navy: #1b3560;
    --sky: #1a9ee0;
    --ink: #444a52;
    --rule: #9a9a9a;
    --band-light: #27a8ec;
    --band-dark: #10336a;
    --back-center: #0aa2e8;
    --back-edge: #0c4386;
    --white: #ffffff;
  }
  * { box-sizing: border-box; margin: 0; padding: 0; }
  html, body { width: 1200px; height: 960px; overflow: hidden; }
  body {
    background: var(--backdrop);
    font-family: "Roboto", sans-serif;
    position: relative;
  }
  .card {
    position: absolute;
    left: 321px;
    width: 599px;
    height: 342px;
    border-radius: 18px;
    overflow: hidden;
  }
  .card-front { top: 110px; background: var(--card-white); }
  .card-back {
    top: 493px;
    background: radial-gradient(ellipse 60% 75% at 50% 45%, var(--back-center) 0%, var(--back-edge) 100%);
  }
  .brand {
    position: absolute;
    right: 34px;
    top: 30px;
    display: flex;
    flex-direction: column;
    align-items: center;
    gap: 10px;
  }
  .brand-dot {
    width: 78px; height: 78px;
    border-radius: 50%;
    border: 6px solid var(--navy);
  }
  .brand-name {
    font-weight: 700;
    font-size: 29px;
    letter-spacing: 4px;
    color: var(--navy);
    line-height: 1;
  }
  .person { position: absolute; left: 37px; top: 193px; }
  .person-name { font-weight: 700; font-size: 22px; color: var(--navy); line-height: 1.1; }
  .person-title { font-weight: 500; font-size: 14px; color: var(--sky); margin-top: 3px; }
  .rule {
    position: absolute; left: 38px; right: 36px; top: 244px;
    height: 1px; background: var(--rule);
  }
  .contacts, .address {
    position: absolute; top: 258px;
    font-size: 14px; color: var(--ink); line-height: 19px;
    list-style: none;
  }
  .contacts { left: 39px; }
  .contacts li { display: flex; align-items: center; gap: 9px; }
  .contacts svg { width: 12px; height: 12px; fill: var(--navy); }
  .address { right: 33px; text-align: right; }
  .front-band {
    position: absolute; left: 0; right: 0; bottom: 0; height: 12px;
    background: linear-gradient(to bottom, var(--band-dark) 0 3px, var(--band-light) 3px 9px, var(--band-dark) 9px);
  }
  .back-mark {
    position: absolute; left: 50%; top: 75px;
    transform: translateX(-50%);
    width: 176px; height: 176px;
    border-radius: 50%;
    border: 12px solid var(--white);
    display: flex; align-items: center; justify-content: center;
  }
  .back-mark span {
    font-weight: 700; font-size: 22px; letter-spacing: 2px; color: var(--white);
  }
  .back-web {
    position: absolute; left: 0; right: 0; top: 290px;
    text-align: center; color: var(--white);
    font-size: 14px; letter-spacing: 6.5px;
  }
</style>
</head>
<body>
  <section class="card card-front">
    <div class="brand">
      <div class="brand-dot"></div>
      <div class="brand-name">SKYVORNQ</div>
    </div>
    <div class="person">
      <div class="person-name">MARCUS HALE</div>
      <div class="person-title">CEO/FOUNDER</div>
    </div>
    <div class="rule"></div>
    <ul class="contacts">
      <li><svg viewBox="0 0 24 24"><path d="M6.6 10.8a15 15 0 0 0 6.6 6.6l2.2-2.2a1 1 0 0 1 1-.25 11.4 11.4 0 0 0 3.6.57 1 1 0 0 1 1 1V20a1 1 0 0 1-1 1A17 17 0 0 1 3 4a1 1 0 0 1 1-1h3.5a1 1 0 0 1 1 1c0 1.25.2 2.45.57 3.57a1 1 0 0 1-.25 1z"/></svg>689 512 7049</li>
      <li><svg viewBox="0 0 24 24"><path d="M7 1h10a2 2 0 0 1 2 2v18a2 2 0 0 1-2 2H7a2 2 0 0 1-2-2V3a2 2 0 0 1 2-2zm0 3v14h10V4zm5 15.5a1.2 1.2 0 1 0 0 2.4 1.2 1.2 0 0 0 0-2.4z"/></svg>836 271 5830</li>
      <li><svg viewBox="0 0 24 24"><path d="M2 5h20v14H2zm2 2v.5l8 5 8-5V7l-8 5z"/></svg>info@skyvornq.com</li>
    </ul>
    <ul class="address">
      <li>4827 Trellis Hollow Road</li>
      <li>Fort Pierce, Florida, 34951</li>
      <li>www.skyvornq.com</li>
    </ul>
    <div class="front-band"></div>
  </section>

  <section class="card card-back">
    <div class="back-mark"><span>SKYVORNQ</span></div>
    <div class="back-web">www.skyvornq.com</div>
  </section>
</body>
</html>
```